Business card for Crestline Bathrooms

Please design a business card for our bathroom renovation business. You can use my existing logo, but if you have an idea to modernize it, I would like to see it. Please see attached files first. I would like to use the blue and the orange theme. I like the concept of using the shower head in the logo. Please find following a design (or two) that I have been trying to create with my limited resources. That design was for a sign, but I was going to adopt it and use it as a business card as well. I like the concept of the water splash but I don’t think it “flows” nicely together with the logo. Another thought is that maybe creating the logo out of water splash could work and have a dramatic effect (like the water text and the butterfly picture attached with similar background instead of white). If the above doesn’t work I would like to see a modern simplified design. One of the attached files named as the unwanted business card has all the details that I want included in the business card. Please note that it is two sided.
Updates

I am very thankful for the designs that I have received, but they are very similar and only a couple of attempts to do something with the water splash as per my original brief. Modernizing the logo and having it made out of out of water splash with the orange as color accent could work and have a dramatic effect (like the water text and the butterfly picture attached with similar background instead of white). Please do not use the butterfly itself! This is just an example that images can be created out of water splash.

Contact Information for Business Card

all the details are on the unwonted business card file included

Colors
3176b5

Requirements
Nice to have
• Copied from the brief:
• ... maybe creating the logo out of water splash could work and have a dramatic effect (like the water text and the butterfly picture attached with similar background instead of white). Please do not use the butterfly itself!
Should not have
• I am getting designs with a butterfly. The butterfly picture was an example of creating something from a water splash. The butterfly itself has no association with anything other than the concept of creating a logo out of water splash. Sorry, I thought I was clear in the brief.

```html
<!DOCTYPE html>
<html lang="en">
<head>
<meta charset="utf-8">
<title>Crestline Bathrooms – Business Card</title>
<link rel="stylesheet" href="https://fonts.googleapis.com/css2?family=Roboto:wght@400;500;700&family=Itim&display=swap">
<style>
  :root {
    --backdrop: #e4e4e4;
    --navy: #1b3152;
    --coral: #e8786a;
    --white: #ffffff;
    --splash-light: rgba(214, 222, 236, 0.85);
    --splash-mid: rgba(120, 140, 175, 0.55);
  }
  * { box-sizing: border-box; margin: 0; padding: 0; }
  html, body {
    width: 1200px; height: 960px; overflow: hidden;
    background: var(--backdrop);
    font-family: "Roboto", Arial, sans-serif;
  }
  .canvas { position: relative; width: 1200px; height: 960px; }
  .card {
    position: absolute; width: 600px; height: 342px;
    background: var(--navy); overflow: hidden;
    box-shadow: 2px 3px 5px rgba(0,0,0,0.35);
  }
  .card--back { left: 303px; top: 125px; }
  .card--front { left: 299px; top: 493px; }

  .splash { position: absolute; top: 0; bottom: 0; }
  .card--back .splash {
    left: 0; width: 280px;
    background:
      radial-gradient(ellipse 90px 140px at 20px 250px, var(--splash-light), transparent 75%),
      radial-gradient(ellipse 140px 200px at 110px 60px, var(--splash-mid), transparent 80%),
      linear-gradient(90deg, var(--splash-mid), transparent 95%);
  }
  .card--front .splash {
    right: 0; width: 310px;
    background:
      radial-gradient(ellipse 90px 150px at 290px 230px, var(--splash-light), transparent 75%),
      radial-gradient(ellipse 150px 90px at 180px 20px, var(--splash-mid), transparent 80%),
      linear-gradient(270deg, var(--splash-mid), transparent 95%);
  }

  .services {
    position: absolute; right: 44px; top: 60px;
    list-style: none; text-align: right;
    color: var(--white); font-size: 15px; line-height: 24.2px;
  }
  .services li::after {
    content: ""; display: inline-block; width: 6px; height: 6px;
    margin-left: 7px; border-radius: 50%; background: var(--coral);
    vertical-align: middle;
  }
  .memberships { position: absolute; left: 376px; top: 260px; display: flex; gap: 28px; align-items: center; }

  .brand {
    position: absolute; left: 112px; top: 62px;
    display: flex; align-items: center; gap: 10px;
    color: var(--white); font-weight: 500; font-size: 30px; letter-spacing: 0.3px;
  }
  .brand__dot { width: 14px; height: 14px; border-radius: 50%; background: var(--coral); }

  .holder {
    position: absolute; left: 30px; top: 172px;
    font-family: "Itim", "Comic Sans MS", cursive;
    font-size: 23px; color: var(--coral); letter-spacing: 0.5px;
  }
  .contacts { position: absolute; left: 31px; top: 208px; list-style: none; color: var(--white); font-size: 17px; }
  .contacts li { display: flex; align-items: center; gap: 7px; height: 21.5px; }
  .contacts svg { width: 14px; height: 14px; flex: none; }
  .contacts .phones { font-weight: 700; font-size: 18px; height: 24px; }
  .phones .sep { margin: 0 12px; font-weight: 400; }
  .abn { position: absolute; left: 50px; top: 307px; color: var(--white); font-size: 10px; }
</style>
</head>
<body>
<main class="canvas">

  <section class="card card--back" aria-label="Card back">
    <div class="splash" role="img" aria-label="Water splash texture"></div>
    <ul class="services">
      <li>Complete Bathroom Renovations &amp; Remodelling</li>
      <li>Professional Service From Concept To Completion</li>
      <li>Highly Skilled &amp; Qualified Tradespeople</li>
      <li>All Work Guaranteed</li>
    </ul>
    <div class="memberships">
      <svg width="32" height="34" viewBox="0 0 32 34" role="img" aria-label="Industry association badge"><rect x="1" y="1" width="30" height="32" rx="6" fill="#fff"/></svg>
      <svg width="118" height="26" viewBox="0 0 118 26" role="img" aria-label="Builders association badge"><rect x="0" y="0" width="22" height="26" fill="#fff"/><rect x="30" y="7" width="86" height="12" fill="#fff" opacity="0.85"/></svg>
    </div>
  </section>

  <section class="card card--front" aria-label="Card front">
    <div class="splash" role="img" aria-label="Water splash texture"></div>
    <div class="brand"><span class="brand__dot"></span>Crestline Bathrooms</div>
    <p class="holder">Daniel Markovic</p>
    <ul class="contacts">
      <li class="phones">
        <svg viewBox="0 0 24 24"><path fill="#e8786a" d="M6.6 10.8a15.2 15.2 0 0 0 6.6 6.6l2.2-2.2c.3-.3.7-.4 1-.2 1.1.4 2.3.6 3.6.6.6 0 1 .4 1 1V20c0 .6-.4 1-1 1A17 17 0 0 1 3 4c0-.6.4-1 1-1h3.5c.6 0 1 .4 1 1 0 1.3.2 2.5.6 3.6.1.3 0 .7-.2 1z"/></svg>
        <span>0400 555 218<span class="sep">|</span>6200 1947</span>
      </li>
      <li>
        <svg viewBox="0 0 24 24"><circle cx="12" cy="12" r="4" fill="none" stroke="#e8786a" stroke-width="2.6"/><path d="M16 8v5.5a2.5 2.5 0 0 0 5 0V12a9 9 0 1 0-3.5 7.1" fill="none" stroke="#e8786a" stroke-width="2.6"/></svg>
        <span>daniel@crestlinebathrooms.com.au</span>
      </li>
      <li>
        <svg viewBox="0 0 24 24"><circle cx="12" cy="12" r="10" fill="#e8786a"/><path d="M2 12h20M12 2c3 3 3 17 0 20M12 2c-3 3-3 17 0 20" stroke="#1b3152" stroke-width="1.6" fill="none"/></svg>
        <span>crestlinebathrooms.com.au</span>
      </li>
      <li>
        <svg viewBox="0 0 24 24"><rect x="1" y="4" width="22" height="16" fill="#e8786a"/><path d="M1 5l11 8 11-8" stroke="#1b3152" stroke-width="1.8" fill="none"/></svg>
        <span>PO Box 41 Larkfield 2620</span>
      </li>
    </ul>
    <p class="abn">ABN 48 210 563 907</p>
  </section>

</main>
</body>
</html>
```